accomplished personal trainer, former elite gymnast from Russia, highly professional and experienced

Established Fitness trainer in California requires a new web site to attract personal clients and build her group exercise classes.

Here is an example of another fitness trainer's site that I really liked the technology:
http://www.tedvorlam.com

Below I have inserted my current web site: www.quelbornfitnesslodi.com
You can use this web site for the principal content, such as my background and qualifications.

Target Market(s)

Anyone who wants to improve their fitness levels and wellness in general. Anyone who needs directions and instruction on how to exercise. I can train anyone from elite athlete to a disabled person.

Industry/Entity Type

Fitness

Coding

Coded - Design and coding required

Number of Pages Required

5+ page

Font styles to use
Sans Serif

Requirements
Must have
• Easy to navigate main info about me, location, services, contact, benefits of using my services.
• Would be great to create unique representation of me as a trainer and a person, using new technologies and new ideas. Make it different from the other websites. Having its own character. Not too complicated and heavy with information, but an eye catching, useful and fun to navigate.
Nice to have
• new technology, easy access to information, the idea of enjoyment of life, lightness about achieving any goal, spiritual wisdom, unique design. I am planning to insert educational videos, advise, maybe jokes. Sign in, shopping cart, logo, should be easy for me to make changes in content.
Should not have
• cliché, outdated technology, too complicated,

```html
<!DOCTYPE html>
<html lang="en">
<head>
<meta charset="utf-8">
<title>Quelborn Fitness Lodi</title>
<link href="https://fonts.googleapis.com/css2?family=Lato:ital,wght@0,400;0,700;1,400&family=Nunito+Sans:wght@600;700&display=swap" rel="stylesheet">
<style>
:root{
  --blue:#1f8ad3;
  --ink:#1d1d1d;
  --text:#6b6b6b;
  --line:#d9d9d9;
  --soft:#f4f4f4;
  --white:#fff;
}
*{box-sizing:border-box;margin:0;padding:0}
html,body{width:1200px;height:3523px;overflow:hidden}
body{font-family:"Lato",sans-serif;color:var(--text);background:var(--white);position:relative}
.abs{position:absolute}
h1,h2,h3{font-family:"Nunito Sans",sans-serif;color:var(--ink);font-weight:700}

/* header */
.topbar{top:0;left:0;width:1200px;height:70px}
.brand{left:98px;top:22px;font-family:"Nunito Sans",sans-serif;font-weight:700;font-size:24px;letter-spacing:1px;color:var(--ink)}
.call{left:606px;top:20px;display:flex;align-items:center;gap:10px;font-size:13px;color:var(--ink)}
.call b{font-size:18px}
.call svg{width:28px;height:28px}
.social{display:flex;gap:8px}
.social span{width:32px;height:32px;border-radius:50%;background:var(--blue);display:block}
.topbar .social{position:absolute;left:946px;top:16px}
.nav{top:70px;left:0;width:1200px;height:40px;border-top:1px solid var(--line);border-bottom:1px solid var(--line)}
.nav ul{list-style:none;display:flex;position:absolute;left:98px;top:10px;gap:46px;font-size:15px;font-weight:700;color:var(--ink)}
.nav li.active{color:var(--blue)}
.search{position:absolute;left:812px;top:0;width:290px;height:38px;border-left:1px solid var(--line);border-right:1px solid var(--line);font-size:14px;color:#aaa;padding:10px 18px}
.search svg{position:absolute;right:14px;top:11px}

/* photo placeholders: layered soft gradients in each photo's main tones */
.photo{left:0;width:1200px}
.hero{top:110px;height:488px;background:
  radial-gradient(ellipse 140px 90px at 560px 250px,rgba(236,92,160,.75),rgba(236,92,160,0)),
  radial-gradient(ellipse 120px 80px at 600px 110px,rgba(240,215,170,.6),rgba(240,215,170,0)),
  radial-gradient(ellipse 330px 50px at 560px 410px,rgba(175,180,205,.55),rgba(175,180,205,0)),
  radial-gradient(ellipse 380px 180px at 150px 60px,rgba(28,50,22,.8),rgba(28,50,22,0)),
  radial-gradient(ellipse 420px 170px at 1000px 90px,rgba(92,60,40,.55),rgba(92,60,40,0)),
  linear-gradient(180deg,#2f4a24 0%,#4f7431 30%,#86b04f 55%,#9ec45e 100%)}
.hero h1{position:absolute;top:152px;width:1200px;text-align:center;color:var(--white);font-size:52px;letter-spacing:1px;text-shadow:0 2px 8px rgba(0,0,0,.25)}
.btn-ghost{position:absolute;left:488px;top:234px;width:223px;height:40px;border:2px solid var(--white);color:var(--white);font-size:14px;font-weight:700;text-align:center;line-height:36px}
.arrow{position:absolute;top:224px}

/* welcome */
.welcome h2{left:98px;top:640px;font-size:29px}
.welcome p{left:98px;width:480px;font-size:12.5px;line-height:22px}
.btn{height:38px;border:1px solid var(--blue);color:var(--blue);font-size:12px;font-weight:700;text-align:center;line-height:36px;letter-spacing:.5px}
.btn.fill{background:var(--blue);color:var(--white)}
.video{left:641px;top:644px;width:460px;height:286px;border:4px solid #e6e6e6;background:
  radial-gradient(ellipse 120px 60px at 190px 120px,rgba(232,82,150,.8),rgba(232,82,150,0)),
  radial-gradient(ellipse 110px 70px at 180px 220px,rgba(225,225,230,.85),rgba(225,225,230,0)),
  radial-gradient(ellipse 120px 50px at 340px 150px,rgba(150,150,175,.6),rgba(150,150,175,0)),
  linear-gradient(170deg,#345a24 0%,#5f8d38 45%,#8ab65a 100%)}
.video svg{position:absolute;left:202px;top:115px}

.band1{top:977px;height:452px;background:
  radial-gradient(ellipse 240px 120px at 640px 270px,rgba(34,150,205,.85),rgba(34,150,205,0)),
  radial-gradient(ellipse 120px 110px at 420px 260px,rgba(238,205,165,.75),rgba(238,205,165,0)),
  radial-gradient(ellipse 130px 160px at 930px 110px,rgba(20,22,30,.75),rgba(20,22,30,0)),
  radial-gradient(ellipse 260px 200px at 1150px 60px,rgba(235,240,225,.8),rgba(235,240,225,0)),
  linear-gradient(120deg,#2f5424 0%,#5f8f3f 45%,#8fbb6c 75%,#c9ddb0 100%)}

/* tips */
.tips-img{left:98px;top:1477px;width:390px;height:319px;border:4px solid #e6e6e6;background:
  radial-gradient(ellipse 130px 100px at 220px 190px,rgba(95,160,60,.9),rgba(95,160,60,0)),
  radial-gradient(ellipse 150px 120px at 220px 190px,rgba(250,250,250,.9) 60%,rgba(250,250,250,0) 62%),
  radial-gradient(circle 40px at 100px 40px,rgba(160,200,60,.9),rgba(160,200,60,0)),
  radial-gradient(circle 30px at 150px 200px,rgba(210,60,40,.8),rgba(210,60,40,0)),
  linear-gradient(140deg,#4a2e1c,#6b4127 60%,#5a3520)}
.tips h2{left:545px;top:1490px;font-size:29px}
.tips ul{left:545px;top:1550px;list-style:none;width:540px;font-size:12.5px;line-height:21px}
.tips li{position:relative;padding-left:28px;margin-bottom:20px}
.tips li svg{position:absolute;left:0;top:3px}

.band2{top:1845px;height:452px;background:
  radial-gradient(ellipse 110px 170px at 170px 340px,rgba(236,90,150,.85),rgba(236,90,150,0)),
  radial-gradient(ellipse 90px 200px at 610px 320px,rgba(25,25,28,.9),rgba(25,25,28,0)),
  radial-gradient(ellipse 300px 40px at 850px 230px,rgba(220,180,150,.6),rgba(220,180,150,0)),
  radial-gradient(ellipse 600px 30px at 600px 180px,rgba(120,110,90,.4),rgba(120,110,90,0)),
  linear-gradient(180deg,#3f6530 0%,#6e9a43 30%,#86b04e 60%,#6f9a40 100%)}

/* testimonials */
.testi h2{top:2343px;width:1200px;text-align:center;font-size:29px}
.quote-mark{left:98px;top:2395px;width:115px;height:115px;border-radius:50%;background:#e4e4e4;color:#c8c8c8;font-family:Georgia,serif;font-size:90px;line-height:140px;padding-left:22px}
.avatar{left:172px;top:2392px;width:105px;height:105px;border-radius:50%;background:linear-gradient(160deg,#b68560,#e3cdb5);border:4px solid var(--white)}
.testi blockquote{left:319px;top:2408px;width:790px;font-style:italic;font-size:13.5px;line-height:28px}
.testi cite{left:319px;top:2512px;font-style:normal;font-weight:700;font-size:13px;color:var(--ink)}
.dots{left:572px;top:2551px;display:flex;gap:8px}
.dots span{width:12px;height:12px;border-radius:50%;background:#d6d6d6}
.dots span:first-child{background:var(--blue)}

.band3{top:2618px;height:451px;background:
  radial-gradient(ellipse 170px 60px at 300px 330px,rgba(230,60,130,.7),rgba(230,60,130,0)),
  radial-gradient(ellipse 160px 90px at 520px 300px,rgba(245,140,70,.75),rgba(245,140,70,0)),
  radial-gradient(ellipse 140px 100px at 780px 290px,rgba(130,235,60,.85),rgba(130,235,60,0)),
  radial-gradient(ellipse 500px 70px at 560px 410px,rgba(30,40,80,.65),rgba(30,40,80,0)),
  radial-gradient(ellipse 80px 260px at 40px 250px,rgba(70,50,35,.8),rgba(70,50,35,0)),
  radial-gradient(ellipse 90px 260px at 1030px 250px,rgba(70,50,35,.75),rgba(70,50,35,0)),
  linear-gradient(180deg,#5d8a30 0%,#a9c766 35%,#7fa64a 70%,#3f6a2c 100%)}

/* contact */
.contact h2{top:3112px;width:1200px;text-align:center;font-size:29px}
.contact h3{font-size:15px;top:3170px}
.field{height:34px;border:1px solid #cfcfcf;font-size:11px;color:#999;padding:10px 12px;letter-spacing:.5px}
.info-icon{left:782px;width:36px;height:36px;border-radius:50%;border:1px solid var(--blue)}
.info-icon svg{position:absolute;left:8px;top:8px}
.info-text{left:862px;font-size:12px;line-height:20px;width:260px}

.footer{top:3452px;left:0;width:1200px;height:71px;background:var(--soft);text-align:center;font-size:12px;line-height:71px;color:#777}
</style>
</head>
<body>

<header class="abs topbar">
  <div class="abs brand">QUELBORN FITNESS LODI</div>
  <div class="abs call">
    <svg viewBox="0 0 28 28"><circle cx="14" cy="14" r="12.5" fill="none" stroke="var(--blue)" stroke-width="1.5"/><path d="M10 8l3 3-1.6 1.6a8 8 0 0 0 4 4L17 15l3 3-2 2c-5 0-10-5-10-10z" fill="var(--blue)"/></svg>
    <span>CALL US ON :</span><b>+1 (555) 014-2280</b>
  </div>
  <div class="social"><span></span><span></span><span></span><span></span></div>
</header>

<nav class="abs nav">
  <ul>
    <li class="active">Home</li><li>Group Classes</li><li>Personal Training</li><li>About Quelborn</li><li>Blog</li><li>Contact</li>
  </ul>
  <div class="search">Search
    <svg width="16" height="16" viewBox="0 0 16 16"><circle cx="6.5" cy="6.5" r="5" fill="none" stroke="#999" stroke-width="1.6"/><path d="M10.5 10.5l4 4" stroke="#999" stroke-width="1.6"/></svg>
  </div>
</nav>

<section class="abs photo hero" role="img" aria-label="Trainer in a pink top doing a split stretch on a lawn under trees">
  <h1>QUELBORN FITNESS LODI</h1>
  <div class="btn-ghost">GET MORE INFO &gt;&gt;</div>
  <svg class="arrow" style="left:40px" width="20" height="36" viewBox="0 0 20 36"><path d="M17 2L3 18l14 16" fill="none" stroke="rgba(255,255,255,.6)" stroke-width="2"/></svg>
  <svg class="arrow" style="left:1140px" width="20" height="36" viewBox="0 0 20 36"><path d="M3 2l14 16L3 34" fill="none" stroke="rgba(255,255,255,.6)" stroke-width="2"/></svg>
</section>

<section class="welcome">
  <h2 class="abs">Welcome to Quelborn Fitness</h2>
  <p class="abs" style="top:692px">Vera Solnikova is the owner of Quelborn Fitness. She was born and raised in Vologda, Russia where she was a competitive gymnast.</p>
  <p class="abs" style="top:766px">Vera graduated from Northfield Academy of Sport with a bachelor degree in Kinesiology and Sports Science. For more than 20 years, Vera has worked as choreographer, gymnastics coach, and fitness professional. Vera has a deep knowledge (theory and experience) in many aspects of wellness.</p>
  <div class="abs btn" style="left:98px;top:883px;width:108px">READ MORE</div>
  <div class="abs video" role="img" aria-label="Video still of trainer doing crunches on an exercise ball in a park">
    <svg width="48" height="48" viewBox="0 0 48 48"><circle cx="24" cy="24" r="21" fill="rgba(0,0,0,.35)" stroke="#fff" stroke-width="3"/><path d="M19 14l14 10-14 10z" fill="#fff"/></svg>
  </div>
</section>

<div class="abs photo band1" role="img" aria-label="Trainer in a blue top smiling while hanging upside down from a tree branch"></div>

<section class="tips">
  <div class="abs tips-img" role="img" aria-label="Fresh salad bowl with tomatoes and green apples on a wooden table"></div>
  <h2 class="abs">Tips to members</h2>
  <ul class="abs">
    <li><svg width="14" height="14" viewBox="0 0 14 14"><circle cx="7" cy="7" r="7" fill="var(--blue)"/><path d="M3.8 7.2l2.2 2.2 4.2-4.4" fill="none" stroke="#fff" stroke-width="1.6"/></svg>Private sessions will provide you with the motivation you need to reach your goals.</li>
    <li><svg width="14" height="14" viewBox="0 0 14 14"><circle cx="7" cy="7" r="7" fill="var(--blue)"/><path d="M3.8 7.2l2.2 2.2 4.2-4.4" fill="none" stroke="#fff" stroke-width="1.6"/></svg>As an NCF certified trainer, Vera will make sure you're working out safely and keep the workouts fresh and exciting so you can achieve your goals.</li>
    <li><svg width="14" height="14" viewBox="0 0 14 14"><circle cx="7" cy="7" r="7" fill="var(--blue)"/><path d="M3.8 7.2l2.2 2.2 4.2-4.4" fill="none" stroke="#fff" stroke-width="1.6"/></svg>Quelborn Group Exercise classes are designed for people of all fitness levels.</li>
    <li><svg width="14" height="14" viewBox="0 0 14 14"><circle cx="7" cy="7" r="7" fill="var(--blue)"/><path d="M3.8 7.2l2.2 2.2 4.2-4.4" fill="none" stroke="#fff" stroke-width="1.6"/></svg>Classes are taught with a variety of approaches.</li>
  </ul>
  <div class="abs btn" style="left:545px;top:1751px;width:108px">READ MORE</div>
  <div class="abs btn fill" style="left:665px;top:1751px;width:130px">JOIN US NOW!</div>
</section>

<div class="abs photo band2" role="img" aria-label="Two women in pink and black tops stretching their arms outdoors in a park"></div>

<section class="testi">
  <h2 class="abs">Client Testimonials</h2>
  <div class="abs quote-mark">“</div>
  <div class="abs avatar" role="img" aria-label="Client portrait"></div>
  <blockquote class="abs">“I have known Vera for many years as a fitness trainer and workout class instructor. She is truly one of the very best in the business. Vera is extremely knowledgeable about human physiology and teaching. Her personality is professional, informative, and caring. She would always put “her all” into each of her classes.</blockquote>
  <cite class="abs">– MARION TELFORD</cite>
  <div class="abs dots"><span></span><span></span><span></span></div>
</section>

<div class="abs photo band3" role="img" aria-label="Group exercise class in bright sportswear stretching together under trees"></div>

<section class="contact">
  <h2 class="abs">Contact Us</h2>
  <h3 class="abs" style="left:98px">Contact Form</h3>
  <div class="abs field" style="left:98px;top:3213px;width:298px">NAME :</div>
  <div class="abs field" style="left:407px;top:3213px;width:298px">PHONE :</div>
  <div class="abs field" style="left:98px;top:3257px;width:607px">EMAIL :</div>
  <div class="abs field" style="left:98px;top:3301px;width:607px;height:72px">YOUR SCRIPT :</div>
  <div class="abs btn fill" style="left:629px;top:3384px;width:76px;height:30px;line-height:28px">SUBMIT</div>

  <h3 class="abs" style="left:782px">Contact Information</h3>
  <div class="abs info-icon" style="top:3214px"><svg width="18" height="18" viewBox="0 0 18 18"><path d="M9 1a6 6 0 0 1 6 6c0 4-6 10-6 10S3 11 3 7a6 6 0 0 1 6-6z" fill="var(--blue)"/><circle cx="9" cy="7" r="2" fill="#fff"/></svg></div>
  <div class="abs info-text" style="top:3212px">14 Arden Lane, Riverton East, Lodi CA 95240, USA</div>
  <div class="abs info-icon" style="top:3270px"><svg width="18" height="18" viewBox="0 0 18 18"><path d="M4 2l3 3-1.5 1.5a7 7 0 0 0 5 5L12 10l3 3-2 2C8 15 3 10 3 4z" fill="var(--blue)"/></svg></div>
  <div class="abs info-text" style="top:3278px">+1 (555) 014-2280</div>
  <div class="abs info-icon" style="top:3326px;background:var(--blue)"><svg width="18" height="18" viewBox="0 0 18 18"><rect x="2" y="4" width="14" height="10" fill="#fff"/><path d="M2 4l7 6 7-6" fill="none" stroke="var(--blue)" stroke-width="1.4"/></svg></div>
  <div class="abs info-text" style="top:3334px">vera@quelbornmail.net</div>
  <div class="abs social" style="left:782px;top:3384px"><span style="width:28px;height:28px"></span><span style="width:28px;height:28px"></span><span style="width:28px;height:28px"></span><span style="width:28px;height:28px"></span></div>
</section>

<footer class="abs footer">Copyrights © 2016, Quelborn Fitness Lodi. All Rights Reserved.</footer>

</body>
</html>
```